Typography of the cover "Watch the tide turning"

We would like to improve the presentation of a book cover: presentation and typography of the authors and of the title. Image of the cover is available in two versions (with or without sky), joined with the texts (joined files): Mathis Corvenot Watched the turning tide Romance Editions Murlane

Industry/Entity Type

Publishing

Colors

Designer to choose colors to be used in the design.

Requirements
Must have
• Provided picture (with or without sky)

```html
<!DOCTYPE html>
<html lang="en">
<head>
<meta charset="utf-8">
<title>Watch the tide turning — Mathis Corvenot</title>
<link rel="stylesheet" href="https://fonts.googleapis.com/css2?family=Anton&family=Montserrat:wght@700;800&display=swap">
<style>
  :root {
    --sky-top: #ececec;
    --sky-mid: #d6d8da;
    --haze: #b4b6b8;
    --city-mid: #6a6a6a;
    --city-dark: #2a2a2a;
    --ink: #161616;
    --paper: #ffffff;
    --frame: #6b1d18;
    --title-dark: #561611;
    --title-light: #e01f26;
  }
  html, body {
    margin: 0;
    padding: 0;
    overflow: hidden;
    background: #ffffff;
  }
  .cover {
    position: relative;
    width: 810px;
    height: 1200px;
    overflow: hidden;
  }
  .cover-photo {
    position: absolute;
    inset: 0;
    background: linear-gradient(180deg,
      var(--sky-top) 0%,
      var(--sky-mid) 35%,
      #e4e6e8 52%,
      var(--haze) 62%,
      var(--city-mid) 78%,
      var(--city-dark) 100%);
  }
  .cover-type {
    position: absolute;
    inset: 0;
  }
  .title-line {
    font-family: "Anton", sans-serif;
    fill: url(#titleFill);
    stroke: var(--paper);
    stroke-width: 4;
    paint-order: stroke;
  }
  .author, .genre, .publisher {
    font-family: "Montserrat", sans-serif;
    font-weight: 800;
  }
  .author {
    font-size: 33px;
    letter-spacing: 0.14em;
    fill: var(--ink);
  }
  .genre {
    font-size: 32px;
    letter-spacing: 0.12em;
    fill: var(--paper);
  }
  .publisher {
    font-size: 21px;
    letter-spacing: 0.1em;
    fill: var(--paper);
  }
</style>
</head>
<body>
  <main class="cover">
    <div class="cover-photo" role="img" aria-label="Black and white photograph of a dense city skyline under a cloudy sky, fading into mist with vertical light streaks"></div>

    <svg class="cover-type" width="810" height="1200" viewBox="0 0 810 1200">
      <defs>
        <linearGradient id="titleFill" gradientUnits="userSpaceOnUse" x1="0" y1="214" x2="0" y2="658">
          <stop offset="0" stop-color="#561611"/>
          <stop offset="0.5" stop-color="#8f1f1b"/>
          <stop offset="1" stop-color="#e01f26"/>
        </linearGradient>
      </defs>

      <g class="frame" stroke="var(--frame)" stroke-width="2" fill="none">
        <polyline points="180,184 102,184 102,703 318,703"/>
        <polyline points="644,184 725,184 725,703 520,703"/>
      </g>

      <text class="author" x="416" y="196" text-anchor="middle" textLength="430" lengthAdjust="spacingAndGlyphs">MATHIS CORVENOT</text>

      <g class="title" text-anchor="middle">
        <text class="title-line" x="414" y="352" font-size="160" textLength="572" lengthAdjust="spacingAndGlyphs">WATCH THE</text>
        <text class="title-line" x="418" y="506" font-size="153" textLength="372" lengthAdjust="spacingAndGlyphs">TIDE</text>
        <text class="title-line" x="412" y="658" font-size="155" textLength="520" lengthAdjust="spacingAndGlyphs">TURNING</text>
      </g>

      <text class="genre" x="418" y="715" text-anchor="middle" textLength="172" lengthAdjust="spacingAndGlyphs">ROMAN</text>

      <text class="publisher" x="417" y="1078" text-anchor="middle" textLength="258" lengthAdjust="spacingAndGlyphs">EDITIONS MURLANE</text>
    </svg>
  </main>
</body>
</html>
```